I need a flyer made , the flyer can be one page or two pages or three pages . I will be posting this on Instagram and social media platforms. I am a luxury home builder , I am looking to hire a construction project manager . Below are some examples and ideas what can be on the flyer

We’re looking for a construction project manager who’s passionate about building luxury homes at the highest standards
We’re hiring construction project manager
* Experience 5+ years in residential project management with a strong portfolio of completed homes.
* location : Bergen County NJ
* excellent leadership skills, leads teams with confidence and clarity
* communicates seamlessly with architects , engineers, designers and clients
*knows how to manage budgets and timelines without compromising quality
*solves problems with a positive solution first mindset
* pays attention to every detail because in luxury the small things are the big things

Apply now , link in bio or DM to connect.

My logo is attached, my web site www.velstridebuilders.com
My style is modern but still warm and inviting. I like a clean classy look .

Please don’t add any images of chairs or people to the flyer , I do not want people on my flyer. Do not add standard images of offices and houses , we are luxury builders , we build homes over 2 million dollars. Keep a classy , simple modern look . High end .

You can add a white hard hat with my logo on it for a image , this is a suggestion does not have to be on my flyer ,

```html
<!DOCTYPE html>
<html lang="en">
<head>
<meta charset="utf-8">
<title>Velstride Builders – Hiring Construction Project Manager</title>
<link rel="stylesheet" href="https://fonts.googleapis.com/css2?family=Barlow+Condensed:ital,wght@1,800&family=Poppins:wght@400;500;600;700&display=swap">
<style>
  :root{
    --bg:#d6d6d6;
    --paper:#f4f4f4;
    --ink:#1f232a;
    --dark:#2b3038;
    --red:#ee3d14;
    --orange:#f7941d;
    --grey:#b9bcc1;
    --text:#26292e;
  }
  *{margin:0;padding:0;box-sizing:border-box}
  html,body{width:1200px;height:839px;overflow:hidden;background:var(--bg);font-family:"Poppins",sans-serif;color:var(--text)}
  .carousel{position:absolute;left:0;top:0;width:1200px;height:839px;display:flex;gap:20px;justify-content:center;align-items:center}
  .post{position:relative;width:376px;height:376px;background:linear-gradient(180deg,#fff 0%,var(--paper) 70%);overflow:hidden;box-shadow:0 4px 14px rgba(0,0,0,.18)}
  .post > *{position:absolute}
  .deco{left:0;top:0;width:376px;height:376px}
  .footer-band{left:0;bottom:0;width:376px;height:64px;background:linear-gradient(180deg,rgba(43,48,56,0) 0%,var(--dark) 55%,var(--ink) 100%)}
  .brand{left:0;bottom:16px;width:180px;text-align:center;font-weight:500;font-size:15px;letter-spacing:1px;color:#fff}
  .brand::before{content:"";display:inline-block;width:8px;height:8px;background:var(--orange);margin-right:6px;vertical-align:1px}
  .photo{display:block}

  /* post 1 */
  .kicker{left:58px;top:18px;font-size:29px;font-weight:500;color:var(--red);letter-spacing:1px}
  .chevrons{left:166px;top:26px;width:34px;height:20px}
  .headline{left:20px;top:40px;font-family:"Barlow Condensed",sans-serif;font-style:italic;font-weight:800;font-size:82px;line-height:1;color:var(--ink);letter-spacing:-1px}
  .role{left:28px;top:122px;font-size:16.5px;line-height:18px;font-weight:500;color:var(--red)}
  .role strong{display:block;font-weight:600;color:var(--ink)}
  .rule{left:0;top:172px;width:200px;height:3px;background:var(--grey)}
  .intro{left:22px;top:198px;width:118px;font-size:10px;line-height:14px}

  /* post 2 */
  .years{left:164px;top:46px;display:flex;align-items:flex-start;gap:4px}
  .years .num{font-size:42px;font-weight:700;color:var(--red);line-height:1}
  .years .label{font-size:22px;font-weight:600;color:var(--red);line-height:1;margin-top:6px}
  .years .label span{display:block;color:var(--ink);font-size:17px;font-weight:500;margin-top:2px;margin-left:-4px}
  .summary{left:103px;top:104px;width:273px;height:32px;border-radius:16px 0 0 16px;background:var(--dark);color:var(--orange);font-size:9.3px;line-height:13px;padding:3px 0 0 32px}
  .divider{left:0;top:147px;width:376px;height:2px;background:var(--grey)}
  .skills{left:20px;top:163px;width:250px;list-style:none}
  .skills li{position:relative;padding-left:16px;font-size:9.6px;line-height:13.5px;margin-bottom:5px}
  .skills li svg{position:absolute;left:0;top:2px;width:10px;height:10px}
  .location{left:282px;top:161px;width:64px;height:64px;border-radius:50%;background:#fff;border:1.5px solid var(--dark);box-shadow:0 0 0 2px #fff,3px 3px 0 1px var(--orange);text-align:center;font-size:7.5px;line-height:10px;padding-top:9px}
  .location svg{width:12px;height:15px;display:block;margin:0 auto 2px}

  /* post 3 */
  .apply{left:176px;top:228px;width:156px;height:30px;border-radius:15px;background:var(--red);color:#fff;font-size:19px;font-weight:700;text-align:center;line-height:30px;letter-spacing:.5px;box-shadow:0 2px 0 var(--ink)}
  .contact{left:200px;top:268px;font-size:10.5px;line-height:16px;font-weight:500;list-style:none}
  .contact li{position:relative}
  .contact svg{position:absolute;left:-16px;top:3px;width:10px;height:10px}
  .web{left:176px;top:325px;width:200px;height:19px;border-radius:10px 0 0 10px;background:var(--orange);color:var(--ink);font-size:10px;line-height:19px;padding-left:18px}
</style>
</head>
<body>
<main class="carousel">

  <!-- Slide 1: headline -->
  <section class="post post-hiring">
    <svg class="deco" viewBox="0 0 376 376">
      <polygon points="280,0 312,0 376,64 376,96" fill="#c4c6ca"/>
      <polygon points="320,0 376,0 376,56" fill="var(--orange)"/>
      <path class="photo" role="img" aria-label="Luxury home exterior with hard hat theme, blended photo" d="M376,60 L376,376 L190,376 C200,280 230,160 330,95 C350,82 362,72 376,60 Z" fill="url(#g1)"/>
      <defs>
        <linearGradient id="g1" x1="0" y1="0" x2="0" y2="1">
          <stop offset="0" stop-color="#e9e4dc"/>
          <stop offset=".5" stop-color="#b89a7a"/>
          <stop offset="1" stop-color="#4b4f55"/>
        </linearGradient>
      </defs>
    </svg>
    <div class="kicker">WE’RE</div>
    <svg class="chevrons" viewBox="0 0 34 20"><path d="M12 3 4 10l8 7M21 3l-8 7 8 7" fill="none" stroke="var(--red)" stroke-width="3"/><path d="M30 3l-8 7 8 7" fill="none" stroke="var(--orange)" stroke-width="3"/></svg>
    <h1 class="headline">HIRING</h1>
    <div class="role">CONSTRUCTION<strong>PROJECT MANAGER</strong></div>
    <div class="rule"></div>
    <p class="intro">We’re looking for a construction project manager who’s passionate about building Luxury homes at the highest standards.</p>
    <div class="footer-band"></div>
    <div class="brand">VELSTRIDE</div>
  </section>

  <!-- Slide 2: requirements -->
  <section class="post post-details">
    <svg class="deco" viewBox="0 0 376 376">
      <defs>
        <linearGradient id="g2" x1="0" y1="0" x2="1" y2="1"><stop offset="0" stop-color="#ece9e3"/><stop offset="1" stop-color="#b9aa94"/></linearGradient>
        <linearGradient id="g3" x1="0" y1="0" x2="1" y2="1"><stop offset="0" stop-color="#f2f1ee"/><stop offset="1" stop-color="#c9b59a"/></linearGradient>
      </defs>
      <path class="photo" role="img" aria-label="Photo of a white luxury home facade" d="M0,0 L186,0 C170,40 120,110 0,134 Z" fill="url(#g2)"/>
      <path d="M0,58 C60,40 120,20 100,0" fill="none" stroke="var(--orange)" stroke-width="2"/>
      <polygon points="276,0 300,0 376,76 376,100" fill="#c4c6ca"/>
      <polygon points="310,0 376,0 376,66" fill="var(--orange)"/>
      <circle cx="330" cy="308" r="76" fill="none" stroke="var(--orange)" stroke-width="2"/>
      <circle class="photo" role="img" aria-label="Bright luxury living room interior" cx="336" cy="312" r="70" fill="url(#g3)"/>
    </svg>
    <div class="years"><span class="num">5+</span><span class="label">YEARS<span>EXPERIENCE</span></span></div>
    <p class="summary">in Residential Project Management with<br>a Strong Portfolio of completed homes.</p>
    <div class="divider"></div>
    <ul class="skills">
      <li><svg viewBox="0 0 10 10"><circle cx="5" cy="5" r="4.4" fill="none" stroke="var(--orange)"/><path d="M3 5l1.5 1.5L7 3.8" fill="none" stroke="var(--orange)"/></svg>Excellent leadership skills, leads teams with confidence and clarity</li>
      <li><svg viewBox="0 0 10 10"><circle cx="5" cy="5" r="4.4" fill="none" stroke="var(--orange)"/><path d="M3 5l1.5 1.5L7 3.8" fill="none" stroke="var(--orange)"/></svg>Communicates seamlessly with architects , engineers, designers and clients</li>
      <li><svg viewBox="0 0 10 10"><circle cx="5" cy="5" r="4.4" fill="none" stroke="var(--orange)"/><path d="M3 5l1.5 1.5L7 3.8" fill="none" stroke="var(--orange)"/></svg>Knows how to manage budgets and timelines without compromising quality</li>
      <li><svg viewBox="0 0 10 10"><circle cx="5" cy="5" r="4.4" fill="none" stroke="var(--orange)"/><path d="M3 5l1.5 1.5L7 3.8" fill="none" stroke="var(--orange)"/></svg>Solves problems with a positive solution first mindset</li>
      <li><svg viewBox="0 0 10 10"><circle cx="5" cy="5" r="4.4" fill="none" stroke="var(--orange)"/><path d="M3 5l1.5 1.5L7 3.8" fill="none" stroke="var(--orange)"/></svg>Pays attention to every detail because in luxury the small things are the big things</li>
    </ul>
    <div class="location">
      <svg viewBox="0 0 12 15"><path d="M6 0a5 5 0 0 0-5 5c0 4 5 10 5 10s5-6 5-10a5 5 0 0 0-5-5z" fill="var(--red)"/><circle cx="6" cy="5" r="2" fill="#fff"/></svg>
      Bergen<br>County NJ
    </div>
    <div class="footer-band"></div>
    <div class="brand">VELSTRIDE</div>
  </section>

  <!-- Slide 3: call to action -->
  <section class="post post-apply">
    <svg class="deco" viewBox="0 0 376 376">
      <defs>
        <linearGradient id="g4" x1="0" y1="0" x2="1" y2="1"><stop offset="0" stop-color="#3a3a3c"/><stop offset=".6" stop-color="#6b5a48"/><stop offset="1" stop-color="#d8d2c8"/></linearGradient>
        <linearGradient id="g5" x1="0" y1="0" x2="1" y2="1"><stop offset="0" stop-color="#f3f3f2"/><stop offset="1" stop-color="#b79877"/></linearGradient>
        <linearGradient id="g6" x1="0" y1="0" x2="1" y2="1"><stop offset="0" stop-color="#e6e4e0"/><stop offset="1" stop-color="#55575b"/></linearGradient>
      </defs>
      <polygon points="276,0 300,0 376,76 376,100" fill="#c4c6ca"/>
      <polygon points="310,0 376,0 376,66" fill="var(--orange)"/>
      <circle cx="100" cy="72" r="124" fill="none" stroke="#d0d1d4" stroke-width="3"/>
      <circle class="photo" role="img" aria-label="Dark stone luxury bathroom interior" cx="100" cy="72" r="120" fill="url(#g4)"/>
      <circle cx="257" cy="132" r="68" fill="none" stroke="var(--orange)" stroke-width="3"/>
      <circle class="photo" role="img" aria-label="White luxury bathroom with wood vanity" cx="257" cy="132" r="57" fill="url(#g5)" stroke="#fff" stroke-width="3"/>
      <circle cx="92" cy="245" r="57" fill="none" stroke="var(--orange)" stroke-width="3"/>
      <circle class="photo" role="img" aria-label="Crystal chandelier detail" cx="92" cy="245" r="46" fill="url(#g6)" stroke="#fff" stroke-width="3"/>
    </svg>
    <div class="apply">APPLY NOW</div>
    <ul class="contact">
      <li><svg viewBox="0 0 10 10"><path d="M4 6 6 4M3 4.5 1.5 6a1.8 1.8 0 0 0 2.5 2.5L5.5 7M7 5.5 8.5 4A1.8 1.8 0 0 0 6 1.5L4.5 3" fill="none" stroke="var(--orange)" stroke-width="1.2"/></svg>Link in Bio</li>
      <li><svg viewBox="0 0 10 10"><circle cx="5" cy="5" r="4.4" fill="none" stroke="var(--orange)"/><path d="M3.8 3.8a1.2 1.2 0 1 1 1.7 1.1c-.4.2-.5.4-.5.8M5 7.3v.2" fill="none" stroke="var(--ink)" stroke-width=".9"/></svg>or DM to connect</li>
    </ul>
    <div class="footer-band"></div>
    <div class="web">www.velstridebuilders.com</div>
    <div class="brand">VELSTRIDE</div>
  </section>

</main>
</body>
</html>
```